Lawn sign for construction company

Would like this to be a very clean and high end design for luxury homes. We need a yard sign designed that includes the company logo, website, phone number and major service offerings (residential and commercial renovations and maintenance)
The company website is brackwellbuilders.com all other contact info is in the attachments
Target Market(s)
Luxury home owners and business owners
Industry/Entity Type
Construction/Home Improvement
Font styles to use
Other font styles liked:
- See company logo and other graphics included for title text fonts. All other fonts can be standard sans serif.
Colors
0054AA
0677BA
7BADD7
CADEEF
E8F1F8
Requirements
Must have
- Clean, easy to read design, would like 2 sided sign. A main sign side and back side which states “free estimates, and includes the website and phone number. Must also match the color scheme of the provided logo and other company images. Dark Navy blue primary color, gray secondary color, and orange as an accent color.
Nice to have
- 2nd sign side very simple design
Should not have
- Too many graphics limit to 1-3 colors

```html
<!DOCTYPE html>
<html lang="en">
<head>
<meta charset="utf-8">
<title>Brackwell Builders – Yard Sign, Two Sides</title>
<link rel="stylesheet" href="https://fonts.googleapis.com/css2?family=Archivo+Black&family=Oswald:wght@500&family=Poppins:wght@400&family=Roboto:wght@700&display=swap">
<style>
  :root {
    --navy: #15106b;
    --orange: #fa6a17;
    --orange-deep: #f25a0c;
    --white: #ffffff;
    --steel: #7d7d80;
    --backdrop: #ead6b4;
    --ink: #111111;
  }
  * { margin: 0; padding: 0; box-sizing: border-box; }
  html, body {
    width: 1200px;
    height: 2848px;
    overflow: hidden;
    background: var(--backdrop);
  }
  .sheet {
    width: 1200px;
    height: 2848px;
    display: flex;
    flex-direction: column;
    align-items: center;
    justify-content: center;
    gap: 36px;
  }
  .side-label {
    font-family: "Roboto", Arial, sans-serif;
    font-weight: 700;
    font-size: 84px;
    line-height: 1;
    color: var(--ink);
    margin-top: 60px;
  }
  .side-label:first-child { margin-top: 0; }
  .sign {
    width: 1080px;
    height: 810px;
    display: block;
    box-shadow: 0 24px 40px rgba(0,0,0,0.28);
  }
  .sign .field { fill: var(--navy); }
  .sign .chevron { fill: var(--orange); }
  .sign .pinstripe { stroke: var(--white); stroke-width: 2; opacity: 0.55; fill: none; }
  .brand-mark { fill: var(--steel); }
  .brand-name {
    font-family: "Archivo Black", Arial, sans-serif;
    font-size: 66px;
    fill: var(--white);
  }
  .headline {
    font-family: "Archivo Black", Arial, sans-serif;
    font-size: 51px;
    fill: var(--white);
  }
  .service-pill { fill: var(--orange); }
  .service-list {
    font-family: "Oswald", Arial, sans-serif;
    font-weight: 500;
    font-size: 31px;
    fill: var(--white);
  }
  .offer-title {
    font-family: "Archivo Black", Arial, sans-serif;
    font-size: 84px;
    fill: var(--white);
  }
  .badge-pill { fill: var(--white); }
  .badge-text {
    font-family: "Poppins", Arial, sans-serif;
    font-weight: 400;
    font-size: 33px;
    fill: var(--navy);
    letter-spacing: 1px;
  }
  .badge-text .amp { fill: var(--orange); }
  .phone-pill { fill: var(--orange); }
  .phone-disc { fill: var(--white); }
  .phone-glyph { fill: var(--navy); }
  .phone-number {
    font-family: "Archivo Black", Arial, sans-serif;
    font-size: 96px;
    fill: var(--white);
  }
  .web-address {
    font-family: "Poppins", Arial, sans-serif;
    font-weight: 400;
    font-size: 58px;
    fill: var(--white);
  }
</style>
</head>
<body>
<main class="sheet">

  <h2 class="side-label">Front Side</h2>
  <svg class="sign sign-front" viewBox="0 0 1080 810" role="img" aria-label="Front of yard sign: Brackwell Builders, residential and commercial renovations and maintenance">
    <rect class="field" width="1080" height="810"/>
    <polygon class="chevron" points="0,0 1080,0 1080,50 540,360 0,50"/>
    <g class="pinstripes">
      <polyline class="pinstripe" points="0,72 540,382 1080,72"/>
      <polyline class="pinstripe" points="0,90 540,400 1080,90"/>
      <polyline class="pinstripe" points="0,108 540,418 1080,108"/>
    </g>
    <rect x="150" y="150" width="780" height="250" fill="var(--navy)"/>
    <circle class="brand-mark" cx="540" cy="200" r="58"/>
    <text class="brand-name" x="540" y="340" text-anchor="middle">BRACKWELL BUILDERS</text>

    <text class="headline" x="540" y="586" text-anchor="middle">RESIDENTIAL AND COMMERCIAL</text>
    <text class="headline" x="540" y="654" text-anchor="middle">RENOVATIONS AND MAINTENANCE</text>

    <rect class="service-pill" x="124" y="686" width="846" height="78" rx="39"/>
    <text class="service-list" x="547" y="737" text-anchor="middle">GENERAL CONTRACTING  |  PROPERTY MANAGEMENT  |  REMODELING</text>
  </svg>

  <h2 class="side-label">Back Side</h2>
  <svg class="sign sign-back" viewBox="0 0 1080 810" role="img" aria-label="Back of yard sign: free estimates, licensed and insured, phone and website">
    <rect class="field" width="1080" height="810"/>
    <polygon class="chevron" points="0,0 1080,0 1080,75 540,383 0,75"/>
    <g class="pinstripes">
      <polyline class="pinstripe" points="0,102 540,410 1080,102"/>
      <polyline class="pinstripe" points="0,128 540,436 1080,128"/>
      <polyline class="pinstripe" points="0,156 540,464 1080,156"/>
    </g>

    <text class="offer-title" x="540" y="126" text-anchor="middle">FREE ESTIMATES</text>
    <rect class="badge-pill" x="322" y="164" width="437" height="68" rx="34"/>
    <text class="badge-text" x="540" y="210" text-anchor="middle">LICENSED <tspan class="amp">&amp;</tspan> INSURED</text>

    <rect class="phone-pill" x="86" y="516" width="882" height="130" rx="65"/>
    <circle class="phone-disc" cx="148" cy="581" r="41"/>
    <path class="phone-glyph" d="M134 558c3-2 6-1 8 2l6 9c1 3 1 5-1 7l-4 3c2 6 7 11 13 14l3-4c2-2 5-2 7-1l9 6c3 2 3 5 1 8l-4 5c-2 3-6 4-10 3-16-5-29-18-34-34-1-4 0-8 3-10z"/>
    <text class="phone-number" x="550" y="617" text-anchor="middle">810-555-0162</text>

    <text class="web-address" x="540" y="732" text-anchor="middle">brackwellbuilders.com</text>
  </svg>

</main>
</body>
</html>
```